BOLD & MINIMALIST DESIGN NEEDED

We want a very bold but minimalistic business card design that is impactful and utilizes both sides of the business card. Our current logo is included for your use.

We want bold fonts and good use of negative space. We don't want the logo to overpower the design.

Target Market(s)

Professionals who are building new commercial buildings.

Industry/Entity Type

Construction

Contact Information for Business Card

Name, Title, email, office phone, cell phone, website

Font styles to use
Serif
Sans Serif

Requirements
Must have
• Bold design!

```html
<!DOCTYPE html>
<html lang="en">
<head>
<meta charset="utf-8">
<title>Ridgeline Build — Business Card</title>
<link rel="stylesheet" href="https://fonts.googleapis.com/css2?family=Poppins:wght@400;600;800&display=swap">
<style>
  :root{
    --backdrop:#262626;
    --card-dark:#1f1f1f;
    --card-dark-edge:#2b2b2b;
    --card-light:#f1f1f1;
    --ink:#1c1c1c;
    --ink-soft:#2a2a2a;
    --paper-text:#f4f4f4;
    --brand-green:#74ad2b;
    --steel:#4a4a4a;
  }
  *{margin:0;padding:0;box-sizing:border-box}
  html,body{width:1200px;height:576px;overflow:hidden;background:var(--backdrop)}
  body{position:relative;font-family:"Poppins",sans-serif}

  .card{position:absolute;top:138px;height:293px;border-radius:10px;overflow:hidden}
  .card--back{left:102px;width:486px;background:var(--card-dark)}
  .card--front{left:596px;width:480px;background:var(--card-light)}

  .accent-band{position:absolute;top:0;bottom:0;width:28px}
  .card--back .accent-band{right:0;background:var(--steel)}
  .card--front .accent-band{left:0;background:var(--brand-green)}

  .brand-name{font-weight:800;text-transform:uppercase;letter-spacing:1px;line-height:1}
  .card--back .brand-name{position:absolute;left:48px;top:128px;font-size:30px;color:var(--paper-text)}
  .card--front .brand-name{position:absolute;right:36px;top:44px;font-size:26px;color:var(--ink)}

  .person{position:absolute;right:36px;top:150px;text-align:right}
  .person__name{font-weight:600;font-size:20px;color:var(--brand-green);line-height:1.2}
  .person__title{font-size:11px;color:var(--ink-soft);margin-top:4px}

  .contact{position:absolute;right:36px;top:212px;list-style:none;text-align:right}
  .contact__item{display:flex;justify-content:flex-end;align-items:center;gap:7px;font-size:11.5px;color:var(--ink-soft);line-height:17px}
  .contact__icon{width:10px;height:10px;flex:none}
</style>
</head>
<body>
  <section class="card card--back" aria-label="Card back">
    <p class="brand-name">Ridgeline Build</p>
    <div class="accent-band"></div>
  </section>

  <section class="card card--front" aria-label="Card front">
    <div class="accent-band"></div>
    <p class="brand-name">Ridgeline Build</p>

    <div class="person">
      <p class="person__name">Marco Reyes</p>
      <p class="person__title">Director</p>
    </div>

    <ul class="contact">
      <li class="contact__item">000-555-0142
        <svg class="contact__icon" viewBox="0 0 10 10" aria-hidden="true"><path fill="#74ad2b" d="M1 3c0-1 1-2 4-2s4 1 4 2v1H7V3H3v1H1zM2 5h6l1 4H1z"/></svg>
      </li>
      <li class="contact__item">marco@ridgelinebuild.com
        <svg class="contact__icon" viewBox="0 0 10 10" aria-hidden="true"><rect x="0.5" y="2" width="9" height="6.5" fill="#74ad2b"/><path d="M0.5 2l4.5 3.5L9.5 2" fill="none" stroke="#f1f1f1" stroke-width="0.9"/></svg>
      </li>
      <li class="contact__item">www.ridgelinebuild.com
        <svg class="contact__icon" viewBox="0 0 10 10" aria-hidden="true"><circle cx="5" cy="5" r="4.5" fill="#74ad2b"/><path d="M0.5 5h9M5 0.5c-2 2.5-2 6.5 0 9M5 0.5c2 2.5 2 6.5 0 9" fill="none" stroke="#f1f1f1" stroke-width="0.7"/></svg>
      </li>
    </ul>
  </section>
</body>
</html>
```